Sophisticated, clean website reflecting my feminine, playful side to sell my abstract art,

I need a website no more than 3 pages to showcase my paintings, a little about me and some contact info. I do abstracts so looking for something a little edgy, yet feminine and current.
Updates

Hi there, These are some artists websites that I Iike: Marnelvoss.com (I like how airy it is) peterwallombry.com garethpolvens.com (I like how it scrolls) I'll need a place for a photo ( a headshot-i do not have it yet so I'll need to be able to upload that later) as well as an area for my bio. Also, it's important that I will be able to upload any new photos and descriptions easily so it should be user friendly. Lastly, I like in a sunny place so would like to have this seem upbeat and playful as that is how i like to paint. thanks-I'm trying to upload my photos now -

Target Market(s)

ppl ages 35-70 who want large scale art for their homes

Industry/Entity Type

art

Coding

Coded - Design and coding required

Number of Pages Required

3 page

Colors

Designer to choose colors to be used in the design.

Requirements
Must have
• photos of my art, a place for my bio, be easy to reach me. tasteful-nothing too "in your face" -my clients are pretty high end and organized. They like clean lines
Nice to have
• sophisticated background, muted tones in the back-similar clean font throughout-no cursive
Should not have
• too many dark areas. Too many blocks of color. Too serious.

```html
<!DOCTYPE html>
<html lang="en">
<head>
<meta charset="utf-8">
<title>Helena Marlowe — Abstract Art</title>
<link rel="stylesheet" href="https://fonts.googleapis.com/css2?family=Questrial&family=Quicksand:wght@300;400&display=swap">
<style>
  :root {
    --ink: #2b2b2b;
    --muted: #555555;
    --rule: #bdbdbd;
    --paper: #ffffff;
    --chevron: #9a9a9a;
    --hero-green: #3f8f3a;
    --hero-teal: #1f6f73;
    --hero-light: #e9efe6;
    --gallery-gold: #d9a933;
    --gallery-blue: #2e5c9c;
    --gallery-red: #a9452a;
    --portrait: #cfcac4;
  }
  * { margin: 0; padding: 0; box-sizing: border-box; }
  html, body { width: 1200px; height: 2856px; overflow: hidden; background: var(--paper); }
  body { position: relative; font-family: "Questrial", sans-serif; color: var(--ink); }

  .site-header { position: absolute; top: 0; left: 0; width: 1200px; height: 160px; }
  .brand { position: absolute; top: 26px; left: 0; width: 1200px; text-align: center;
    font-family: "Questrial", sans-serif; font-size: 38px; letter-spacing: 3px; color: var(--ink); }
  .brand-mark { display: inline-block; width: 18px; height: 18px; background: var(--ink); margin: 0 14px; vertical-align: 6px; }
  .main-nav { position: absolute; top: 112px; left: 0; width: 1200px; }
  .main-nav a { position: absolute; font-size: 15px; letter-spacing: 1px; color: var(--ink); text-decoration: none; transform: translateX(-50%); white-space: nowrap; padding-bottom: 8px; }
  .main-nav a.active { border-bottom: 2px solid var(--ink); }

  .hero { position: absolute; top: 160px; left: 0; width: 1200px; height: 656px;
    background:
      radial-gradient(ellipse at 35% 40%, var(--hero-green) 0%, transparent 45%),
      radial-gradient(ellipse at 70% 30%, var(--hero-teal) 0%, transparent 40%),
      radial-gradient(ellipse at 85% 75%, #8a6a4a 0%, transparent 35%),
      linear-gradient(135deg, var(--hero-light), #c9dcc4 50%, #e2e6e0); }
  .slider-arrow { position: absolute; }

  .section-title { position: absolute; font-family: "Quicksand", sans-serif; font-weight: 300; font-size: 56px; letter-spacing: 2px; color: var(--ink); }
  .section-title::after { content: ""; position: absolute; left: 0; right: 0; bottom: -10px; height: 1px; background: var(--rule); }

  .portrait { position: absolute; top: 980px; left: 80px; width: 360px; height: 388px;
    background: linear-gradient(180deg, #e8e6e3, var(--portrait) 60%, #f2f2f2); }
  .about-title { top: 960px; left: 492px; }
  .bio { position: absolute; top: 1068px; left: 492px; width: 620px; font-size: 16px; line-height: 24px; color: var(--muted); }
  .bio p + p { margin-top: 12px; }

  .gallery-title { top: 1530px; left: 0; width: 1200px; text-align: center; }
  .gallery-title::after { left: 470px; right: 470px; }
  .gallery-piece { position: absolute; top: 1664px; left: 160px; width: 872px; height: 536px;
    background:
      radial-gradient(circle at 20% 70%, var(--gallery-gold) 0%, transparent 30%),
      radial-gradient(circle at 80% 75%, var(--gallery-gold) 0%, transparent 28%),
      radial-gradient(ellipse at 50% 30%, var(--gallery-blue) 0%, transparent 40%),
      radial-gradient(circle at 30% 55%, var(--gallery-red) 0%, transparent 22%),
      linear-gradient(160deg, #f2efe8, #e7e2d6); }

  .contact-title { top: 2340px; left: 0; width: 1200px; text-align: center; }
  .contact-title::after { left: 450px; right: 450px; }
  .contact-item { position: absolute; top: 2520px; width: 240px; transform: translateX(-50%); text-align: center; font-size: 17px; color: var(--ink); }
  .contact-item svg { display: block; margin: 0 auto 18px; }

  .site-footer { position: absolute; top: 2772px; left: 0; width: 1200px; border-top: 1px solid #e3e3e3; padding-top: 30px; text-align: center; font-size: 13px; color: var(--muted); }
</style>
</head>
<body>
  <header class="site-header">
    <div class="brand">HELENA<span class="brand-mark"></span>MARLOWE</div>
    <nav class="main-nav">
      <a class="active" href="#" style="left:312px">HOME</a>
      <a href="#" style="left:492px">ABOUT ME</a>
      <a href="#" style="left:688px">GALLERY</a>
      <a href="#" style="left:888px">CONTACT ME</a>
    </nav>
  </header>

  <div class="hero" role="img" aria-label="Featured abstract painting with green, teal and brown brushstrokes on white"></div>
  <svg class="slider-arrow" style="left:14px;top:440px" width="24" height="44" viewBox="0 0 24 44"><polyline points="20,4 4,22 20,40" fill="none" stroke="#ffffff" stroke-width="3"/></svg>
  <svg class="slider-arrow" style="left:1162px;top:440px" width="24" height="44" viewBox="0 0 24 44"><polyline points="4,4 20,22 4,40" fill="none" stroke="#ffffff" stroke-width="3"/></svg>

  <section class="about">
    <div class="portrait" role="img" aria-label="Artist headshot"></div>
    <h2 class="section-title about-title">ABOUT ME</h2>
    <div class="bio">
      <p>Lorem ipsum dolor sit amet, consectetur adipiscing elit, sed do eiusmod tempor incididunt ut labore et dolore magna aliqua. Ut enim ad minim veniam, quis nostrud exercitation Lorem ipsum dolor sit amet, consectetur adipiscing elit, sed do eiusmod tempor incididunt ut labore et dolore.</p>
      <p>Duis aute irure dolor in reprehenderit in voluptate velit esse cillum dolore eu fugiat nulla pariatur. Excepteur sint occaecat cupidatat non proident, sunt in culpa qui officia deserunt mollit anim id est laborum.</p>
      <p>Sed ut perspiciatis unde pariatur. Excepteur sint occaecat cupidatat non proident, sunt in culpa qui officia deserunt mollit anim id est laborum.</p>
    </div>
  </section>

  <section class="gallery">
    <h2 class="section-title gallery-title">GALLERY</h2>
    <div class="gallery-piece" role="img" aria-label="Abstract painting with golden spirals, blue and red strokes on cream"></div>
    <svg class="slider-arrow" style="left:88px;top:1906px" width="24" height="44" viewBox="0 0 24 44"><polyline points="20,4 4,22 20,40" fill="none" stroke="var(--chevron)" stroke-width="3"/></svg>
    <svg class="slider-arrow" style="left:1088px;top:1906px" width="24" height="44" viewBox="0 0 24 44"><polyline points="4,4 20,22 4,40" fill="none" stroke="var(--chevron)" stroke-width="3"/></svg>
  </section>

  <section class="contact">
    <h2 class="section-title contact-title">CONTACT ME</h2>
    <div class="contact-item" style="left:260px">
      <svg width="40" height="40" viewBox="0 0 40 40"><rect x="4" y="9" width="32" height="22" fill="none" stroke="var(--ink)" stroke-width="2"/><polyline points="4,9 20,22 36,9" fill="none" stroke="var(--ink)" stroke-width="2"/></svg>
      info@helenamarlowe.com
    </div>
    <div class="contact-item" style="left:540px">
      <svg width="40" height="40" viewBox="0 0 40 40"><path d="M10 5 L16 5 L18 13 L14 16 Q17 23 24 26 L27 22 L35 24 L35 30 Q34 35 28 35 Q6 32 5 11 Q5 5 10 5 Z" fill="none" stroke="var(--ink)" stroke-width="2" stroke-linejoin="round"/></svg>
      Phone: (123) 456 7890
    </div>
    <div class="contact-item" style="left:780px">
      <svg width="40" height="40" viewBox="0 0 40 40"><circle cx="20" cy="20" r="14" fill="none" stroke="var(--ink)" stroke-width="2"/></svg>
      @hmarloweart
    </div>
    <div class="contact-item" style="left:1004px">
      <svg width="40" height="40" viewBox="0 0 40 40"><rect x="7" y="7" width="26" height="26" fill="none" stroke="var(--ink)" stroke-width="2"/></svg>
      @hmpainter
    </div>
  </section>

  <footer class="site-footer">© 2022 Helena Marlowe &nbsp;All Rights Reserved</footer>
</body>
</html>
```